Lantern Petals Website v.1 - attract floral shop franchisees

I need a simple information website for my new business. We are a franchisor of flower shops. The overall purpose of the website is to promote the company and the service, especially to potential franchisees and retailers. Only about 4 pages are required including homepage, About, For Supermarkets, For Franchisees, and Contact. No special functions are required except the site will have two separate inquiry forms that must be filled out online and submitted via automated email. Similarly, an email form should be linked from the Contact page. I have a logo and business cards designed by ArtMingle, and I would like the site to have a consistent color scheme and style. The key to design will be to express the joy and love associated with flowers and floral bouquets.
IMPORTANT - I will be exporting the website design to Wordpress CMS in a site hosted by HostNimbus. For smooth integration into WordPress hosted by HostNimbus, the designer should build the site using a WordPress-friendly format. Ideally, they should use HTML, CSS, and PHP. Creating a custom theme or using a page builder that exports to WordPress-compatible files is best. This ensures the site can be easily imported and managed within WordPress.

Target Market(s)

Potential franchisees (existing florists or creative types who might like to own a floral business) and supermarkets who might want us to run their floral department

Industry/Entity Type

Floral retailing

Requirements
Must have
• A brand theme that is beautiful, consistent throughout and builds on the logo design
Nice to have
• Show gender and ethnic diversity in customers and florists. Pictures of happy florists (for franchisees) and pictures of amazing floral department displays (for supermarkets)

```html
<!DOCTYPE html>
<html lang="en">
<head>
<meta charset="utf-8">
<title>Lantern Petals</title>
<link href="https://fonts.googleapis.com/css2?family=Figtree:wght@400;500;600&family=Oswald:wght@600&family=Playball&display=swap" rel="stylesheet">
<style>
:root{
  --green:#17902f;
  --orange:#f29f05;
  --cream:#fcf4e4;
  --ink:#2b2b2b;
  --muted:#4a4a4a;
  --dark:#0b0b0b;
  --white:#ffffff;
}
*{box-sizing:border-box;margin:0;padding:0}
html,body{width:1200px;height:3155px;overflow:hidden}
body{position:relative;background:var(--white);font-family:"Figtree",sans-serif;color:var(--ink)}
.abs{position:absolute}
.brand{display:flex;align-items:center;gap:10px;font-family:"Figtree",sans-serif;font-weight:600;color:var(--orange)}
.brand-dot{border-radius:50%;background:var(--orange)}
.header-contact{display:flex;align-items:center;gap:12px;font-size:15px;color:var(--ink)}
.icon-badge{width:36px;height:36px;border-radius:50%;background:var(--orange);display:flex;align-items:center;justify-content:center;box-shadow:0 0 0 3px #fde3b0;flex:none}
.nav{top:98px;left:0;width:1200px;height:43px;background:var(--green)}
.nav a{position:absolute;top:13px;color:var(--white);font-size:13px;text-decoration:none}
.nav .active{font-weight:600}
.nav .active::after{content:"";position:absolute;left:50%;bottom:-8px;width:4px;height:4px;margin-left:-2px;border-radius:50%;background:var(--orange)}
.nav .sep{position:absolute;top:12px;color:var(--white);font-size:13px}
.hero{top:141px;left:0;width:1200px;height:530px;background:radial-gradient(ellipse at 55% 25%,#c9a98a 0%,#8a6a52 35%,#4a3a30 70%,#2e2520 100%)}
.hero-title{top:437px;left:0;width:1200px;text-align:center;font-family:"Oswald",sans-serif;font-weight:600;font-size:47px;line-height:62px;color:var(--white);letter-spacing:-1px}
.btn{background:var(--orange);color:var(--white);border-radius:22px;font-size:14px;font-weight:500;display:flex;align-items:center;justify-content:center}
.script{font-family:"Playball",cursive;color:var(--ink)}
.script span{color:var(--orange)}
.divider{width:124px;height:2px;background:var(--green)}
.body-text{font-size:13px;line-height:23px;color:var(--muted);letter-spacing:.25px}
.body-text p+p{margin-top:8px}
.photo-ring{border-radius:50%;background:var(--white);box-shadow:0 0 18px rgba(0,0,0,.12)}
.photo{background:linear-gradient(160deg,#6d5a4a,#3f3a33 55%,#8a6d5c)}
.band{top:1442px;left:0;width:1200px;height:337px;background:linear-gradient(180deg,#2a2a2a,#3a2a2c 50%,#1f2420)}
.band-text{top:1630px;left:150px;width:900px;text-align:center;color:#eee;font-size:13px;line-height:23px;letter-spacing:.25px}
.partner{top:1555px;left:0;width:1200px;justify-content:center;display:flex;align-items:center;gap:10px;color:#ddd;font-size:15px;font-weight:600;letter-spacing:6px}
.gallery-card{top:1864px;height:270px;border-radius:10px;border:4px solid var(--white);box-shadow:0 0 10px rgba(0,0,0,.15)}
.t-card{top:2361px;width:290px;height:352px;background:var(--cream);border-radius:18px}
.t-quote{position:absolute;top:82px;left:30px;width:230px;text-align:center;font-size:13px;line-height:23px;color:var(--ink);letter-spacing:.3px}
.t-name{position:absolute;top:272px;width:100%;text-align:center;font-family:"Playball",cursive;font-size:21px}
.t-name span{color:var(--orange)}
.stars{position:absolute;top:304px;width:100%;text-align:center;color:var(--orange);font-size:15px;letter-spacing:3px}
.avatar{top:2325px;width:72px;height:72px;border-radius:50%;border:4px solid var(--white);box-shadow:0 0 8px rgba(0,0,0,.12)}
.arrow{width:34px;height:34px;border-radius:50%;display:flex;align-items:center;justify-content:center}
.footer{top:2802px;left:0;width:1200px;height:353px;background:var(--dark);color:var(--white)}
.footer-head{font-family:"Playball",cursive;font-size:20px;color:var(--white)}
.footer-divider{width:60px;height:1px;background:#ccc;margin-top:8px}
.footer-links a{display:block;color:var(--white);text-decoration:none;font-size:13px;line-height:33px}
.contact-row{display:flex;align-items:center;gap:14px;font-size:13px;line-height:18px}
.social{display:flex;gap:8px}
.social span{width:30px;height:30px;border-radius:50%;border:1.5px solid var(--white)}
.rule{top:3108px;left:141px;width:918px;height:1px;background:#444}
.copyright{top:3124px;left:0;width:1200px;text-align:center;font-size:13px}
</style>
</head>
<body>

<header>
  <div class="abs brand" style="top:30px;left:141px;font-size:30px;">
    <span class="brand-dot" style="width:34px;height:34px;"></span>Lantern Petals
  </div>
  <div class="abs header-contact" style="top:31px;left:671px;">
    <span class="icon-badge"><svg width="16" height="16" viewBox="0 0 24 24"><path fill="#fff" d="M6.6 10.8a15 15 0 0 0 6.6 6.6l2.2-2.2c.3-.3.7-.4 1-.2 1.1.4 2.3.6 3.6.6.6 0 1 .4 1 1V20c0 .6-.4 1-1 1A17 17 0 0 1 3 4c0-.6.4-1 1-1h3.5c.6 0 1 .4 1 1 0 1.3.2 2.5.6 3.6.1.3 0 .7-.2 1z"/></svg></span>
    123-456-7890
  </div>
  <div class="abs header-contact" style="top:31px;left:845px;">
    <span class="icon-badge"><svg width="16" height="16" viewBox="0 0 24 24"><path fill="#fff" d="M3 5h18v14H3z"/><path d="M3 6l9 7 9-7" stroke="#f29f05" stroke-width="2" fill="none"/></svg></span>
    info@lanternpetals.com
  </div>
</header>

<nav class="abs nav">
  <a class="active" style="left:141px;">Home</a>
  <span class="sep" style="left:243px;">|</span>
  <a style="left:316px;">About Us</a>
  <span class="sep" style="left:438px;">|</span>
  <a style="left:512px;">For Supermarkets</a>
  <span class="sep" style="left:686px;">|</span>
  <a style="left:758px;">For Franchisees</a>
  <span class="sep" style="left:919px;">|</span>
  <a style="left:992px;">Contact Us</a>
</nav>

<section>
  <div class="abs hero" role="img" aria-label="Smiling florist in a flower shop surrounded by bouquets"></div>
  <h1 class="abs hero-title">Freshest Flowers, Artisan Designs &amp;<br>Franchise Opportunities</h1>
  <div class="abs btn" style="top:582px;left:529px;width:142px;height:40px;">Contact Us</div>
</section>

<section>
  <div class="abs photo-ring" style="top:744px;left:147px;width:440px;height:440px;"></div>
  <div class="abs photo" style="top:753px;left:156px;width:422px;height:422px;border-radius:50%;" role="img" aria-label="Florist arranging lilies and roses in a shop"></div>
  <h2 class="abs script" style="top:744px;left:637px;font-size:50px;font-weight:400;">About <span>Us</span></h2>
  <div class="abs divider" style="top:815px;left:637px;"></div>
  <div class="abs body-text" style="top:849px;left:637px;width:402px;">
    <p>Fresh flowers convey beauty and love, and in our view should become something every person regularly enjoys. Lantern Petals is an entrepreneurial company created to make top quality fresh flowers and professionally-designed bouquets accessible to every consumer at affordable prices.</p>
    <p>Professional florists typically sell the finest quality stems, design the most beautiful bouquets and provide the finest customer service, but their costs – of floral products, retail spaces, labor and marketing – force them to pass high prices along to customers. Supermarket flower departments benefit from high customer footfall, economies of scale and low pricing, but their quality of stems and bouquets is typically poor, staffing is limited, and staff turnover is high which can result in inefficiency, wastage, poorly merchandised selections and limited service.</p>
  </div>
  <div class="abs body-text" style="top:1216px;left:150px;width:900px;text-align:center;">
    <p>Lantern Petals brings the best of professional florists and supermarkets together for the benefit of consumers. It supports a national network of owner-operator franchisees, who in many cases are multi-site professional florists, with comprehensive services to enhance franchise profitability. Lantern Petals works with some of the country's largest and most progressive supermarkets to provide franchisee ownership and operation of their strategically important floral departments.</p>
    <p>Supermarkets find that Lantern Petals is able to improve their financial outcomes, provide attentive customer service and satisfaction, and lift the quality of the entire store environment.</p>
  </div>
</section>

<section>
  <div class="abs band" role="img" aria-label="Dimly lit flower market with buckets of roses"></div>
  <div class="abs partner"><span style="width:14px;height:14px;border-radius:50%;background:#ddd;"></span>FROSTVALE GROUP</div>
  <p class="abs band-text">Lantern Petals operates in partnership with Frostvale Group, the leading franchisor of sushi stations and pre-packaged fruit &amp; vegetable departments to supermarkets across the United States and United Kingdom. Lantern Petals' combination of floral and supermarket franchising expertise guarantees that consumers, franchisees and supermarket partners each receive exceptional service and value.</p>
</section>

<section>
  <div class="abs gallery-card" style="left:141px;width:214px;background:linear-gradient(160deg,#d8d2c8,#b83a4e 55%,#6a3a2c);" role="img" aria-label="Bouquet of roses and hydrangeas"></div>
  <div class="abs gallery-card" style="left:387px;width:213px;background:linear-gradient(160deg,#e6e2da,#c77b8a 50%,#4f6a3a);" role="img" aria-label="Florist arranging flowers in buckets"></div>
  <div class="abs gallery-card" style="left:618px;width:212px;background:linear-gradient(180deg,#3c5a3c,#c58a8e 55%,#6e7a5a);" role="img" aria-label="Flower shop storefront with displays"></div>
  <div class="abs gallery-card" style="left:847px;width:212px;background:linear-gradient(160deg,#ece6de,#9c2f2f 50%,#e8e2d2);" role="img" aria-label="Happy florist in apron behind flowers"></div>
</section>

<section>
  <h2 class="abs script" style="top:2212px;left:0;width:1200px;text-align:center;font-size:50px;font-weight:400;">What Our Customers <span>Say</span></h2>
  <div class="abs divider" style="top:2286px;left:538px;"></div>

  <div class="abs arrow" style="top:2521px;left:92px;border:2px solid var(--green);"><svg width="10" height="10" viewBox="0 0 10 10"><path d="M6.5 1.5L3 5l3.5 3.5" stroke="#222" stroke-width="2" fill="none"/></svg></div>
  <div class="abs arrow" style="top:2521px;left:1074px;background:var(--green);"><svg width="10" height="10" viewBox="0 0 10 10"><path d="M3.5 1.5L7 5 3.5 8.5" stroke="#fff" stroke-width="2" fill="none"/></svg></div>

  <div class="abs t-card" style="left:141px;">
    <p class="t-quote">"Lorem ipsum dolor sit amet, consectetur adipiscing elit, sed do eiusmod tempor incididunt ut labore et dolore magna aliqua. Ut enim ad minim veniam, quis nostrud exercitation ullamco laboris nisi ut aliquip ex ea commodo consequat.</p>
    <div class="t-name">Martin <span>Hale</span></div>
    <div class="stars">★★★★★</div>
  </div>
  <div class="abs t-card" style="left:455px;">
    <p class="t-quote">"Lorem ipsum dolor sit amet, consectetur adipiscing elit, sed do eiusmod tempor incididunt ut labore et dolore magna aliqua. Ut enim ad minim veniam, quis nostrud exercitation ullamco laboris nisi ut aliquip ex ea commodo consequat.</p>
    <div class="t-name">Nina <span>Brooks</span></div>
    <div class="stars">★★★★★</div>
  </div>
  <div class="abs t-card" style="left:769px;">
    <p class="t-quote">"Lorem ipsum dolor sit amet, consectetur adipiscing elit, sed do eiusmod tempor incididunt ut labore et dolore magna aliqua. Ut enim ad minim veniam, quis nostrud exercitation ullamco laboris nisi ut aliquip ex ea commodo consequat.</p>
    <div class="t-name">Peter <span>Lane</span></div>
    <div class="stars">★★★★★</div>
  </div>
  <div class="abs avatar" style="left:250px;background:linear-gradient(180deg,#e8e8e8,#f2b8c0);" role="img" aria-label="Customer portrait"></div>
  <div class="abs avatar" style="left:564px;background:linear-gradient(180deg,#e88a6a,#6fb7d8);" role="img" aria-label="Customer portrait"></div>
  <div class="abs avatar" style="left:878px;background:linear-gradient(180deg,#e8e8e8,#8a8f96);" role="img" aria-label="Customer portrait"></div>
</section>

<footer class="abs footer">
  <div class="abs" style="top:50px;left:141px;">
    <div class="footer-head">Quick Links</div>
    <div class="footer-divider"></div>
    <nav class="footer-links" style="margin-top:12px;">
      <a>Home</a><a>About Us</a><a>For Supermarkets</a><a>For Franchisees</a><a>Contact Us</a>
    </nav>
  </div>
  <div class="abs" style="top:50px;left:410px;">
    <div class="footer-head">Contact Details</div>
    <div class="footer-divider"></div>
    <div class="contact-row" style="margin-top:22px;">
      <span class="icon-badge"><svg width="14" height="16" viewBox="0 0 24 24"><path fill="#fff" d="M12 2a7 7 0 0 0-7 7c0 5 7 13 7 13s7-8 7-13a7 7 0 0 0-7-7zm0 9.5A2.5 2.5 0 1 1 12 6.5a2.5 2.5 0 0 1 0 5z"/></svg></span>
      <span>123, Building Name, Street<br>City, State XY 123456</span>
    </div>
    <div class="contact-row" style="margin-top:16px;">
      <span class="icon-badge"><svg width="16" height="16" viewBox="0 0 24 24"><path fill="#fff" d="M6.6 10.8a15 15 0 0 0 6.6 6.6l2.2-2.2c.3-.3.7-.4 1-.2 1.1.4 2.3.6 3.6.6.6 0 1 .4 1 1V20c0 .6-.4 1-1 1A17 17 0 0 1 3 4c0-.6.4-1 1-1h3.5c.6 0 1 .4 1 1 0 1.3.2 2.5.6 3.6.1.3 0 .7-.2 1z"/></svg></span>
      <span>123-456-7890</span>
    </div>
    <div class="contact-row" style="margin-top:16px;">
      <span class="icon-badge"><svg width="16" height="16" viewBox="0 0 24 24"><path fill="#fff" d="M3 5h18v14H3z"/><path d="M3 6l9 7 9-7" stroke="#f29f05" stroke-width="2" fill="none"/></svg></span>
      <span>info@lanternpetals.com</span>
    </div>
  </div>
  <div class="abs brand" style="top:120px;left:790px;font-size:36px;">
    <span class="brand-dot" style="width:40px;height:40px;"></span>Lantern Petals
  </div>
  <div class="abs social" style="top:214px;left:851px;" aria-label="Social media links">
    <span></span><span></span><span></span><span></span>
  </div>
</footer>
<div class="abs rule"></div>
<p class="abs copyright" style="color:var(--white);">©2024 Lantern Petals. All Rights Reserved.</p>

</body>
</html>
```